Business Card Design For A Renovation Contractor Company

We need a business card for a new company based in Singapore, our company name is "RB Tolvane". We are a renovation contractor that builds designs into reality. We build more of F&B restaurants, retail stores and commercial offices. We work very closely with designers. The final design should communicate to our client that we are a company that you can trust, that will plan and complete your project without giving you a headache. I like my client to remember my company as "RB". The beauty of SIMPLE is important.

Industry/Entity Type

Contractor

Requirements
Nice to have
• Black or Red base

```html
<!DOCTYPE html>
<html lang="en">
<head>
<meta charset="utf-8">
<title>RB Tolvane – Business Card</title>
<link rel="stylesheet" href="https://fonts.googleapis.com/css2?family=Source+Sans+3:wght@400;600;700&display=swap">
<style>
  :root {
    --red: #e41b23;
    --black: #111111;
    --white: #ffffff;
    --grey-text: #333333;
    --rule: #c9c9c9;
    --stage: #ecebe8;
  }
  * { margin: 0; padding: 0; box-sizing: border-box; }
  html, body {
    width: 1200px; height: 720px; overflow: hidden;
    background: var(--stage);
    font-family: "Source Sans 3", "Helvetica Neue", Arial, sans-serif;
  }
  .stage {
    width: 1200px; height: 720px;
    display: flex; align-items: center; justify-content: center; gap: 40px;
  }
  .card {
    position: relative;
    width: 540px; height: 309px;
    overflow: hidden;
    box-shadow: 0 6px 18px rgba(0,0,0,0.18);
  }

  /* Front */
  .card--front { background: var(--white); }
  .card__bands { position: absolute; inset: 0; width: 540px; height: 309px; }
  .brand {
    position: absolute; left: 40px; top: 92px;
    display: flex; align-items: center; gap: 10px;
  }
  .brand__dot {
    width: 26px; height: 26px; border-radius: 50%;
    background: var(--red);
  }
  .brand__name {
    font-size: 40px; font-weight: 600; color: var(--black);
    letter-spacing: -0.5px; line-height: 1;
  }
  .tagline {
    position: absolute; left: 42px; top: 146px;
    width: 230px;
    border-top: 1.5px solid var(--black);
    padding-top: 2px;
    font-size: 16px; color: var(--grey-text); letter-spacing: 0.3px;
  }
  .address {
    position: absolute; left: 40px; top: 232px;
    font-size: 14px; color: var(--grey-text); letter-spacing: 0.2px;
  }
  .contact {
    position: absolute; left: 345px; top: 30px;
    padding-left: 14px;
    border-left: 1px solid var(--rule);
    height: 118px;
  }
  .contact__name { font-size: 17px; font-weight: 700; color: var(--black); line-height: 1.1; }
  .contact__title { font-size: 12px; color: var(--red); margin-bottom: 10px; }
  .contact__list { list-style: none; }
  .contact__item {
    display: flex; align-items: center; gap: 7px;
    font-size: 13px; color: var(--grey-text); line-height: 1.45;
  }
  .contact__icon { width: 10px; height: 10px; fill: var(--red); flex: none; }
  .web--front {
    position: absolute; right: 26px; top: 236px;
    font-size: 14px; color: var(--white); letter-spacing: 1px;
  }

  /* Back */
  .card--back { background: var(--red); }
  .back__brand {
    position: absolute; left: 0; right: 0; top: 110px;
    display: flex; align-items: center; justify-content: center; gap: 14px;
  }
  .back__dot {
    width: 34px; height: 34px; border-radius: 50%;
    background: var(--black);
  }
  .back__name {
    font-size: 50px; font-weight: 600; color: var(--black);
    line-height: 1; letter-spacing: -0.5px;
  }
  .web--back {
    position: absolute; left: 0; right: 0; top: 238px;
    text-align: center;
    font-size: 16px; color: var(--white); letter-spacing: 3px;
  }
</style>
</head>
<body>
<main class="stage">
  <section class="card card--front" aria-label="Business card front">
    <svg class="card__bands" viewBox="0 0 540 309" aria-hidden="true">
      <path d="M0 262 L345 262 C370 262 375 222 405 222 L540 222 L540 228 L410 228 C380 228 375 268 350 268 L0 268 Z" fill="var(--red)"/>
      <path d="M0 268 L350 268 C375 268 380 228 410 228 L540 228 L540 309 L0 309 Z" fill="var(--black)"/>
    </svg>

    <div class="brand">
      <span class="brand__dot"></span>
      <span class="brand__name">RB Tolvane</span>
    </div>
    <p class="tagline">designs built to completion</p>
    <p class="address">Street Name, City Name, State Zip Code</p>

    <div class="contact">
      <p class="contact__name">Your Name</p>
      <p class="contact__title">Title</p>
      <ul class="contact__list">
        <li class="contact__item">
          <svg class="contact__icon" viewBox="0 0 10 10" aria-hidden="true"><path d="M2 0.5 L3.6 0.5 L4.2 2.8 L3 3.6 C3.6 5 5 6.4 6.4 7 L7.2 5.8 L9.5 6.4 L9.5 8 C9.5 9 8.6 9.6 7.6 9.4 C4.2 8.6 1.4 5.8 0.6 2.4 C0.4 1.4 1 0.5 2 0.5 Z"/></svg>
          123-456-0789
        </li>
        <li class="contact__item">
          <svg class="contact__icon" viewBox="0 0 10 10" aria-hidden="true"><path d="M2.5 0 H7.5 A1 1 0 0 1 8.5 1 V9 A1 1 0 0 1 7.5 10 H2.5 A1 1 0 0 1 1.5 9 V1 A1 1 0 0 1 2.5 0 Z M3 1.5 V7.5 H7 V1.5 Z"/></svg>
          123-456-0789
        </li>
        <li class="contact__item">
          <svg class="contact__icon" viewBox="0 0 10 10" aria-hidden="true"><path d="M0 2 H10 V8.5 H0 Z M0.8 2.6 L5 5.6 L9.2 2.6 Z" fill-rule="evenodd"/></svg>
          info@rbtolvane.com
        </li>
      </ul>
    </div>

    <p class="web--front">www.rbtolvane.com</p>
  </section>

  <section class="card card--back" aria-label="Business card back">
    <div class="back__brand">
      <span class="back__dot"></span>
      <span class="back__name">RB Tolvane</span>
    </div>
    <p class="web--back">www.rbtolvane.com</p>
  </section>
</main>
</body>
</html>
```